Hip surgeon needs a educative book cover design

I need to re-design my old book cover for its 3rd edition.
It's a small book dedicated to my patients, who underwent total hip replacement. It's meant to help people getting around the basic care after a total hip replacement surgery and getting back to their normal, active life.
The title is: "Morning light rituals: a quiet companion".
I already had a new logo, new stationery and new website design from ArtFolio (please see the attachments).
The final design should be look alike the other fresh new designs. It must communicate health, peacefulness.
I also attached the manual as it looks today for reference.
A5 size.
Just cover and back cover.
Health

```html
<!DOCTYPE html>
<html lang="en">
<head>
<meta charset="utf-8">
<title>Morning Light Rituals – Cover and Back Cover</title>
<link rel="stylesheet" href="https://fonts.googleapis.com/css2?family=Oswald:wght@400;500;600;700&family=Roboto+Condensed:wght@400;700&family=Roboto:wght@400&display=swap">
<style>
  :root {
    --canvas: #e9e9e7;
    --brand-blue: #4a72b8;
    --brand-blue-light: #5b86c9;
    --paper: #ffffff;
    --paper-shade: #f3f4f6;
    --text-blue: #3f68ad;
    --art-white: #f2f4fa;
    --art-pale: #d5def2;
    --art-mid: #aebfe6;
    --art-deep: #8ea4d6;
  }
  * { margin: 0; padding: 0; box-sizing: border-box; }
  html, body {
    width: 1200px;
    height: 800px;
    overflow: hidden;
    background: var(--canvas);
  }
  .spread {
    position: absolute;
    left: 178px;
    top: 122px;
    width: 850px;
    height: 576px;
    display: flex;
    box-shadow: 0 6px 18px rgba(0,0,0,0.12);
  }
  .page {
    position: relative;
    width: 425px;
    height: 576px;
    background: var(--paper);
    overflow: hidden;
  }

  /* Back cover */
  .back-cover .band {
    position: absolute;
    left: 0; right: 0;
    background: linear-gradient(90deg, var(--brand-blue), var(--brand-blue-light));
  }
  .back-cover .band-top { top: 0; height: 68px; }
  .back-cover .band-bottom { bottom: 0; height: 70px; }
  .author-portrait {
    position: absolute;
    left: 147px;
    top: 118px;
    width: 134px;
    height: 162px;
    border: 3px solid var(--brand-blue);
    border-radius: 10px;
    background: linear-gradient(160deg, #e8e4dc 0%, #d9d6d0 55%, #c9ccd4 100%);
  }
  .brand-mark {
    position: absolute;
    display: flex;
    align-items: center;
    gap: 6px;
    font-family: 'Roboto', sans-serif;
    color: var(--text-blue);
  }
  .brand-mark .dot {
    border-radius: 50%;
    background: var(--brand-blue);
    flex: none;
  }
  .back-cover .brand-mark { left: 141px; top: 298px; }
  .back-cover .brand-mark .dot { width: 26px; height: 26px; }
  .brand-name { font-size: 13px; line-height: 1.1; display: block; }
  .brand-tagline { font-size: 10px; line-height: 1.1; display: block; }
  .back-blurb {
    position: absolute;
    left: 57px;
    top: 350px;
    width: 313px;
    font-family: 'Roboto Condensed', sans-serif;
    font-weight: 700;
    font-size: 10.2px;
    line-height: 11.4px;
    color: var(--text-blue);
    text-align: justify;
    text-align-last: center;
  }

  /* Front cover */
  .front-cover .title-block {
    position: absolute;
    left: 0; top: 0;
    width: 425px;
    height: 198px;
    background: var(--brand-blue);
    color: var(--paper);
    font-family: 'Oswald', sans-serif;
    text-align: center;
  }
  .title-main {
    position: absolute;
    top: 14px;
    left: 0; right: 0;
    font-weight: 700;
    font-size: 50px;
    line-height: 56px;
    letter-spacing: 0.5px;
  }
  .title-rule {
    position: absolute;
    left: 60px;
    right: 62px;
    top: 142px;
    height: 3px;
    background: var(--paper);
  }
  .title-sub {
    position: absolute;
    top: 148px;
    left: 0; right: 0;
    font-weight: 500;
    font-size: 31px;
    line-height: 40px;
    letter-spacing: 0.5px;
  }
  .cover-illustration {
    position: absolute;
    left: 0;
    top: 198px;
    width: 425px;
    height: 308px;
    background: linear-gradient(115deg,
      var(--art-pale) 0%,
      var(--art-mid) 22%,
      var(--art-white) 40%,
      var(--art-deep) 58%,
      var(--art-pale) 74%,
      var(--art-white) 100%);
  }
  .front-cover .brand-mark { left: 14px; top: 520px; gap: 8px; }
  .front-cover .brand-mark .dot { width: 34px; height: 34px; }
  .front-cover .brand-name { font-size: 17px; }
  .front-cover .brand-tagline { font-size: 13px; }
  .front-note {
    position: absolute;
    left: 213px;
    top: 506px;
    width: 212px;
    height: 60px;
    padding: 5px 8px;
    background: var(--brand-blue);
    color: var(--paper);
    font-family: 'Roboto Condensed', sans-serif;
    font-weight: 700;
    font-size: 9px;
    line-height: 11px;
    text-align: justify;
  }
</style>
</head>
<body>
  <main class="spread">
    <section class="page back-cover" aria-label="Back cover">
      <div class="band band-top"></div>
      <div class="author-portrait" role="img" aria-label="Portrait photograph of the surgeon in a white coat"></div>
      <div class="brand-mark">
        <span class="dot"></span>
        <span>
          <span class="brand-name">Dr. Elias R. Moreno</span>
          <span class="brand-tagline">Cirurgia do Quadril</span>
        </span>
      </div>
      <p class="back-blurb">This small companion gathers the gentle habits that help you rest, move and recover after surgery. Each page offers simple steps for the first mornings at home, quiet exercises for strength and balance, and practical advice for sleeping, dressing, bathing and walking with confidence. Read it slowly, return to it often, and share it with the family and friends who care for you. Recovery is a steady path, taken one calm morning at a time, and every small ritual brings you closer to the active, independent life you enjoy.</p>
      <div class="band band-bottom"></div>
    </section>

    <section class="page front-cover" aria-label="Front cover">
      <header class="title-block">
        <h1 class="title-main">MORNING LIGHT<br>RITUALS</h1>
        <div class="title-rule"></div>
        <h2 class="title-sub">A QUIET COMPANION</h2>
      </header>
      <div class="cover-illustration" role="img" aria-label="Blue-toned illustration of a pelvis with a hip implant and a separate femoral stem"></div>
      <div class="brand-mark">
        <span class="dot"></span>
        <span>
          <span class="brand-name">Dr. Elias R. Moreno</span>
          <span class="brand-tagline">Cirurgia do Quadril</span>
        </span>
      </div>
      <p class="front-note">A gentle guide for your first weeks at home, with calm routines, simple daily movements and clear, practical advice to help you rest well and return, step by step, to a steady and active life.</p>
    </section>
  </main>
</body>
</html>
```